We’re a real estate firm that has landed a big builder in a neighboring state. Our branding needs...

We are a real estate firm who represents various builders along with doing resale here in Oregon. Our firm is growing to represent a big builder in Washington State and we’ll have another 40 brokers on our team. We need rebranding. As in, a new logo ( the house logo we have now looks cartoonish, hate it). We need new cards, something to really stand out. I’ve been thinking of using those NFC cards from ZEP or the ones with the seam color. I likely want two or three designs, a darker (as in a background color of black or grey) , a light one ( again I mean background color) and a credit card style (either plastic w an embossed name/number on front, or metal ). I’m thinking dark background for cc, or silver if it’s metal. That’s my thoughts, but you are the artists, so maybe you have an idea I haven’t considered. Our colors were black and red, but we don’t have to stick to that. Just nothing too busy. Oh, and we are typically representing the local, higher quality builders in our area (just below custom), but not national. Subdivisions are near the Kell Varney, Brisco, and Thornfield Crest sites. We are super excited, but without a lot of time to change the “look” of our brokerage. So I’ll be deciding and moving forward within 24 hours tops. Our name is Real Estate Summit Alliance ( we cant change the name because of timeline and business license) Thank you!

Industry/Entity Type

Real Estate

Contact Information for Business Card

The usual. Name of firm. Name of cardholder. Contact info.

Font styles to use
Serif
Sans Serif

Colors

Designer to choose colors to be used in the design.

Requirements
Must have
• A sleek or simple look. I included photos of cards with stylistic attributes we like. Thank you
Nice to have
• We really like the black backgrounds. With foil or embossed detail. We also like the black on black. Matte black card with raised shiny black detail. But still eye catching.
Should not have
• No ornate or busy looking style. We don’t want anything cluttered.

```html
<!DOCTYPE html>
<html lang="en">
<head>
<meta charset="utf-8">
<title>Real Estate Summit Alliance – Business Card</title>
<link rel="stylesheet" href="https://fonts.googleapis.com/css2?family=Lato:wght@400;700;900&family=Arimo:wght@400;700&display=swap">
<style>
  :root {
    --backdrop: #dcd8d3;
    --navy: #0f3163;
    --white: #ffffff;
    --rule: rgba(255,255,255,0.45);
    --shadow: rgba(0,0,0,0.35);
  }
  * { margin: 0; padding: 0; box-sizing: border-box; }
  html, body {
    width: 1200px; height: 900px; overflow: hidden;
    background: var(--backdrop);
  }
  .stage { position: relative; width: 1200px; height: 900px; }
  .card {
    position: absolute;
    box-shadow: 2px 3px 5px var(--shadow);
  }
  .card--front {
    left: 330px; top: 90px; width: 555px; height: 343px;
    background: var(--navy);
    color: var(--white);
    text-align: center;
    font-family: "Arimo", Arial, sans-serif;
  }
  .holder-name {
    position: absolute; left: 0; right: 0; top: 62px;
    font-family: "Lato", sans-serif; font-weight: 700;
    font-size: 20px; letter-spacing: 0.2px; line-height: 24px;
  }
  .holder-title {
    position: absolute; left: 0; right: 0; top: 86px;
    font-size: 16px; line-height: 20px;
  }
  .card--front .divider {
    position: absolute; left: 180px; width: 195px; height: 1px;
    background: var(--rule);
  }
  .divider--upper { top: 116px; }
  .divider--lower { top: 222px; }
  .contact-list {
    position: absolute; left: 0; right: 0; top: 130px;
    list-style: none; font-size: 16px; line-height: 20.3px;
  }
  .contact-list b { font-weight: 700; }
  .address {
    position: absolute; left: 0; right: 0; top: 240px;
    font-style: normal; font-size: 16px; line-height: 20px;
  }
  .card--back {
    left: 330px; top: 469px; width: 559px; height: 343px;
    background: var(--white);
  }
  .brand {
    position: absolute; left: 0; right: 0; top: 110px;
    display: flex; flex-direction: column; align-items: center;
  }
  .brand-mark {
    width: 46px; height: 46px; background: var(--navy); margin-bottom: 36px;
  }
  .brand-name {
    font-family: "Lato", sans-serif; font-weight: 900;
    color: var(--navy); text-align: center;
    font-size: 36px; line-height: 38px;
  }
</style>
</head>
<body>
<main class="stage">
  <section class="card card--front">
    <div class="holder-name">JONAH PEMBERTON</div>
    <div class="holder-title">Managing Director</div>
    <div class="divider divider--upper"></div>
    <ul class="contact-list">
      <li><b>P:</b> 503-555-0142</li>
      <li><b>M:</b> 503-555-0187</li>
      <li><b>E:</b> info@summitalliance.example</li>
      <li><b>W:</b> www.summitalliance.example</li>
    </ul>
    <div class="divider divider--lower"></div>
    <address class="address">12345, Address Goes Here<br>Country Name, 123456.</address>
  </section>

  <section class="card card--back">
    <div class="brand">
      <div class="brand-mark"></div>
      <div class="brand-name">Real Estate<br>Summit Alliance</div>
    </div>
  </section>
</main>
</body>
</html>
```